Business card for a new cabinet shop company named Veloran Cabinets for high end cabinets

Design a business card, thinking dark rich green with colours to speak of high end luxury ie; cream, gold, black possibly

Mitchell Tarrowby
Director Craftsman
Email: info@veloranjoinery-example.com.au
Instagram : @veloran.cabinets

```html
<!DOCTYPE html>
<html lang="en">
<head>
<meta charset="utf-8">
<title>Veloran Cabinets — Business Card</title>
<link rel="stylesheet" href="https://fonts.googleapis.com/css2?family=Montserrat:wght@400;500;700&display=swap">
<style>
  :root {
    --stage: #2b2b2b;
    --card-green: #1f4a3f;
    --pattern-green: #1c4439;
    --gold: #c9a461;
    --cream: #f4f1ea;
    --rule: rgba(244, 241, 234, 0.85);
  }
  * { box-sizing: border-box; margin: 0; padding: 0; }
  html, body {
    width: 1200px;
    height: 694px;
    overflow: hidden;
    background: var(--stage);
    font-family: "Montserrat", Arial, sans-serif;
  }
  .stage {
    position: relative;
    width: 1200px;
    height: 694px;
  }
  .card {
    position: absolute;
    top: 189px;
    width: 540px;
    height: 316px;
    border-radius: 22px;
    background: var(--card-green);
    overflow: hidden;
  }
  .card--front { left: 40px; }
  .card--back { left: 620px; }

  /* Front */
  .front-pattern {
    position: absolute;
    inset: 0;
    background: linear-gradient(135deg, var(--pattern-green), var(--card-green));
  }
  .front-wordmark {
    position: absolute;
    left: 0;
    right: 0;
    top: 142px;
    text-align: center;
    color: var(--gold);
    font-weight: 500;
    font-size: 26px;
    letter-spacing: 1px;
  }

  /* Back */
  .back-wordmark {
    position: absolute;
    right: 34px;
    top: 40px;
    color: var(--gold);
    font-weight: 500;
    font-size: 30px;
    letter-spacing: 1px;
  }
  .rule {
    position: absolute;
    height: 1px;
    background: var(--rule);
  }
  .rule--top { left: 190px; right: 34px; top: 108px; }
  .rule--bottom { left: 34px; width: 250px; top: 238px; }

  .social {
    position: absolute;
    right: 34px;
    top: 124px;
    display: flex;
    align-items: center;
    gap: 8px;
    color: var(--cream);
    font-size: 13px;
  }
  .social-mark {
    width: 12px;
    height: 12px;
    border: 1.5px solid var(--gold);
    border-radius: 3px;
  }

  .person {
    position: absolute;
    left: 34px;
    top: 178px;
  }
  .person-name {
    color: var(--gold);
    font-weight: 700;
    font-size: 22px;
    line-height: 1.1;
  }
  .person-role {
    color: var(--cream);
    font-size: 13px;
    margin-top: 6px;
  }

  .contact {
    position: absolute;
    left: 34px;
    top: 250px;
    list-style: none;
    color: var(--cream);
    font-size: 12.5px;
  }
  .contact-item {
    display: flex;
    align-items: center;
    gap: 9px;
    height: 22px;
  }
  .contact-icon { width: 13px; height: 13px; flex: none; }
</style>
</head>
<body>
<main class="stage">

  <section class="card card--front" aria-label="Card front">
    <div class="front-pattern" role="img" aria-label="Tone-on-tone embossed repeating brand pattern"></div>
    <p class="front-wordmark">Veloran Cabinets</p>
  </section>

  <section class="card card--back" aria-label="Card back">
    <p class="back-wordmark">Veloran Cabinets</p>
    <div class="rule rule--top"></div>

    <p class="social">
      <span class="social-mark" aria-hidden="true"></span>
      @veloran.cabinets
    </p>

    <div class="person">
      <h1 class="person-name">Mitchell Tarrowby</h1>
      <p class="person-role">Director Craftsman</p>
    </div>

    <div class="rule rule--bottom"></div>

    <ul class="contact">
      <li class="contact-item">
        <svg class="contact-icon" viewBox="0 0 16 16" aria-hidden="true">
          <rect x="1" y="3" width="14" height="10" fill="#c9a461"/>
          <path d="M1 3 L8 9 L15 3" fill="none" stroke="#1f4a3f" stroke-width="1.5"/>
        </svg>
        info@veloranjoinery-example.com.au
      </li>
      <li class="contact-item">
        <svg class="contact-icon" viewBox="0 0 16 16" aria-hidden="true">
          <path d="M8 1 C4.7 1 2.5 3.4 2.5 6.3 C2.5 10 8 15 8 15 C8 15 13.5 10 13.5 6.3 C13.5 3.4 11.3 1 8 1 Z" fill="#c9a461"/>
          <circle cx="8" cy="6.3" r="2" fill="#1f4a3f"/>
        </svg>
        Western Australia
      </li>
    </ul>
  </section>

</main>
</body>
</html>
```